Web Design Project

We are an online tax Continuing education provider. We provide online courses for tax preparers. We want the front end page to be user friendly and for the buyer to know exactly what they are looking at. We want a front end page to look smiliar www.larkvalefiling.com. It should have a similar feel to this one.
Our website address will be www.7782QX.com
We currently have another website that is www.LedgrUMs.com but we do not want it to look like this. We want a different look but same information.
We have a logo already which is attached. We don't have specific colors in mind for the front page but don't want it to be too busy looking. It should stand out but not too simple either.
Target Market(s)
Tax Preparers. More serious and professional but these folks are usually not tech savy. Simple, easy to use, and functional is key.
Industry/Entity Type
Education
Requirements
Must have
- Use standard HTML & CSS. NO other coding is needed.
We are looking for 5-7 pages including Home page, log in, FAQ.
Please look at our current website www.LedgrUMs.com and also www.larkvalefiling.com

```html
<!DOCTYPE html>
<html lang="en">
<head>
<meta charset="utf-8">
<title>7782QX – Continuing Education</title>
<link rel="stylesheet" href="https://fonts.googleapis.com/css2?family=Arimo:ital,wght@0,400;0,700;1,400&family=Oswald:wght@700&display=swap">
<style>
:root{
  --navy:#0f2a5c;
  --navy-mid:#1c4585;
  --nav-top:#2d8fd0;
  --nav-bot:#0c5fa6;
  --lime:#d8e45a;
  --brown:#9a4a1a;
  --price:#8a3a10;
  --blue-link:#1a6bb0;
  --text:#555;
  --soft:#f3f3f3;
  --line:#d8d8d8;
  --green-top:#8fd04a;
  --green-bot:#4e9d1c;
  --footer:#333;
}
*{box-sizing:border-box;margin:0;padding:0}
html,body{width:1200px;height:1169px;overflow:hidden;background:#fff}
body{position:relative;font-family:"Arimo",Arial,sans-serif;color:var(--text)}
.abs{position:absolute}
ul{list-style:none}

.site-header{position:absolute;left:0;top:0;width:1200px;height:214px;
  background:radial-gradient(ellipse 320px 220px at 170px 80px,#3a78b8 0%,var(--navy-mid) 45%,var(--navy) 100%)}
.brand{left:96px;top:40px;display:flex;align-items:center;gap:10px;color:#fff;font-size:38px;font-weight:700}
.brand-dot{width:34px;height:34px;border-radius:50%;background:#5eb0e0}
.headline{left:523px;top:20px;font-size:27px;color:var(--lime)}
.perks{left:523px;top:72px;display:flex;gap:30px;font-size:18px;color:var(--lime)}
.perks li{display:flex;align-items:center;gap:4px}
.tagline{left:523px;top:116px;font-size:21px;color:#fff}
.contact-line{left:543px;top:181px;font-size:16px;color:#fff}
.contact-line b{font-weight:400;color:var(--lime)}
.contact-line .sep{color:var(--lime);margin:0 16px}
.hero-photo{left:950px;top:0;width:150px;height:214px;
  background:linear-gradient(180deg,#e8c98a 0%,#2a68c8 55%,#1a4fae 100%)}

.main-nav{position:absolute;left:0;top:214px;width:1200px;height:54px;
  background:linear-gradient(var(--nav-top),var(--nav-bot))}
.main-nav ul{position:absolute;left:90px;top:0;display:flex;height:54px;border-left:1px solid #0b4f8c}
.main-nav li{height:54px;border-right:1px solid #0b4f8c;box-shadow:inset -1px 0 0 #4aa4dd;
  display:flex;align-items:center;justify-content:center;color:#fff;font-size:14px}
.search{position:absolute;left:848px;top:10px;width:263px;height:33px;border-radius:17px;background:#fff;
  font-size:13px;color:#888;padding:10px 0 0 22px}
.search svg{position:absolute;right:18px;top:10px}

.package{left:90px;top:287px;width:1020px;height:407px;background:var(--soft);border-radius:4px}
.pkg-title{left:110px;top:296px;font-size:22px;color:var(--brown)}
.bullets li{position:relative;padding-left:14px;font-size:14px;height:25px}
.bullets li::before{content:"";position:absolute;left:0;top:7px;width:4px;height:4px;border-radius:50%;background:#888}
.bul-left{left:113px;top:345px}
.bul-right{left:528px;top:345px}
.price-box{left:882px;top:313px;width:214px;height:138px;background:#fff;border-radius:3px}
.provider{left:12px;top:18px;width:96px;font-size:11px;text-align:center;line-height:16px}
.price{left:116px;top:2px;font-family:"Oswald",sans-serif;font-size:50px;color:var(--price)}
.register-btn{left:11px;top:69px;width:188px;height:45px;border:1px solid #4b8a22;border-radius:2px;
  background:linear-gradient(var(--green-top),var(--green-bot));color:#1f4c0a;font-size:22px;
  display:flex;align-items:center;justify-content:center;letter-spacing:.5px}
.divider{left:106px;top:474px;width:988px;height:1px;background:var(--line)}
.more-title{left:111px;top:497px;font-size:17px;color:var(--blue-link)}
.more-list{left:113px;top:539px;width:745px}
.more-list li{height:31px;line-height:18px}
.more-list li.two{height:auto}
.req-box{left:882px;top:490px;width:214px;height:178px;background:#fff;border-radius:3px;font-size:11px;line-height:17px}
.req-box p{padding:0 12px}
.req-intro{text-align:center;padding-top:12px!important;height:70px;border-bottom:1px solid var(--line)}
.req-main{color:var(--brown);font-size:12px;padding:4px 12px 6px 14px!important;border-bottom:1px solid var(--line)}
.req-list{padding:6px 12px 0 22px!important}

.promo{top:702px;height:50px;background:var(--soft);font-size:17px;color:var(--brown);padding:14px 0 0 25px}
.promo-a{left:90px;width:500px}
.promo-b{left:609px;width:501px}

.col-head{top:783px;height:42px;border-bottom:1px solid var(--line);font-size:21px;color:#777;display:flex;align-items:center;gap:14px}
.col-1{left:90px;width:311px}
.col-2{left:443px;width:314px}
.col-3{left:800px;width:312px;padding-left:22px}
.vrule{top:777px;width:1px;height:152px;background:var(--line)}
.icon-chip{width:30px;height:30px;border-radius:50%;background:#c9c9c9}
.slider-arrows{position:absolute;right:4px;top:14px}
.quote{left:90px;top:842px;width:290px;font-size:12px;font-style:italic;line-height:21px;color:#666;padding-left:20px}
.quote-mark{font-size:28px;color:#aaa;position:absolute;left:0;top:-8px;font-style:normal}
.author{left:111px;top:914px;font-size:14px;color:#1a4fa0}
.who-text{left:444px;top:842px;width:313px;font-size:12px;line-height:21px;text-align:justify}
.badge{left:814px;top:841px;width:82px;height:89px;background:#1e8ad6}
.why-text{left:920px;top:842px;width:150px;font-size:12px;line-height:21px}

.info-bar{left:90px;top:960px;width:1020px;height:63px;border-radius:3px;
  background:linear-gradient(#2d93d4,#0c5ba0)}
.info-bar span{position:absolute;left:63px;top:20px;color:#fff;font-size:17px}
.bulletin-btn{position:absolute;left:626px;top:14px;width:314px;height:34px;border-radius:17px;
  background:linear-gradient(var(--green-top),var(--green-bot));border:1px solid #3d7d18;
  color:#fff;font-size:14px;font-weight:700;display:flex;align-items:center;justify-content:center;letter-spacing:.5px}

.ssl-badge{left:90px;top:1045px;width:88px;height:49px;background:#8b5a2b;border:1px solid #5a3a18}
.accreditor{left:204px;top:1043px;display:flex;align-items:center;gap:8px;color:#888;font-size:13px;line-height:15px}
.accreditor i{display:block;width:50px;height:50px;border:3px solid #999}
.partner{left:453px;top:1054px;font-size:24px;color:#888}
.footer-nav{right:90px;top:1068px;display:flex;font-size:13px;color:#222}
.footer-nav li+li::before{content:"|";margin:0 10px}
.site-footer{left:0;top:1107px;width:1200px;height:62px;background:var(--footer)}
.copyright{left:90px;top:23px;font-size:13px;color:#bbb}
.social{left:1054px;top:20px;display:flex;gap:8px}
.social i{display:block;width:24px;height:24px;border-radius:3px;background:#3b7bc4}
</style>
</head>
<body>

<header class="site-header">
  <div class="abs brand"><span class="brand-dot"></span>7782QX</div>
  <h1 class="abs headline" style="font-weight:400">Continning Education made simple!</h1>
  <ul class="abs perks">
    <li><svg width="22" height="20" viewBox="0 0 22 20"><circle cx="10" cy="10" r="8" fill="none" stroke="#d8e45a" stroke-width="2"/><path d="M6 10l4 4 10-12" fill="none" stroke="#d8e45a" stroke-width="2.5"/></svg>Fast</li>
    <li><svg width="22" height="20" viewBox="0 0 22 20"><circle cx="10" cy="10" r="8" fill="none" stroke="#d8e45a" stroke-width="2"/><path d="M6 10l4 4 10-12" fill="none" stroke="#d8e45a" stroke-width="2.5"/></svg>Easy</li>
    <li><svg width="22" height="20" viewBox="0 0 22 20"><circle cx="10" cy="10" r="8" fill="none" stroke="#d8e45a" stroke-width="2"/><path d="M6 10l4 4 10-12" fill="none" stroke="#d8e45a" stroke-width="2.5"/></svg>Low Cost</li>
  </ul>
  <p class="abs tagline">Completely Online! “Self-paced”</p>
  <p class="abs contact-line"><b>Call us :</b> 800-555-0142 <span class="sep">|</span><b>E-mail :</b> info@7782qx.com</p>
  <div class="abs hero-photo" role="img" aria-label="Photo of a student holding study books"></div>
</header>

<nav class="main-nav">
  <ul>
    <li style="width:94px">Home</li>
    <li style="width:108px">Courses</li>
    <li style="width:83px">FAQ</li>
    <li style="width:133px">Testimonials</li>
    <li style="width:103px">Contact</li>
    <li style="width:101px">Sign In</li>
    <li style="width:108px">Register</li>
  </ul>
  <div class="search">Search
    <svg width="14" height="14" viewBox="0 0 14 14"><circle cx="5" cy="5" r="4" fill="none" stroke="#999" stroke-width="1.5"/><path d="M8 8l5 5" stroke="#999" stroke-width="2"/></svg>
  </div>
</nav>

<main>
  <section class="abs package"></section>
  <h2 class="abs pkg-title" style="font-weight:400">15-Hour package for IRS Registered Tax-Preparer Continuing Education :</h2>
  <ul class="abs bullets bul-left">
    <li>Ethics (2 hrs CE Credit)</li>
    <li>Charitable Contributions 101 (3 hrs CE Credit)</li>
    <li>Earned Income Credit (2 hrs CE Credit)</li>
    <li>Deducting Transportation Expenses (2 hrs CE Credit)</li>
  </ul>
  <ul class="abs bullets bul-right">
    <li>Employee Health Benefits (1 hr CE Credit)</li>
    <li>Federal Tax Law Updates 2012 (3 hrs CE Credit)</li>
    <li>Business Travel and Entertainment (2 hrs CE Credit)</li>
  </ul>

  <div class="abs price-box">
    <p class="abs provider">Provided by 7782 Education, LLC</p>
    <p class="abs price">$42</p>
    <div class="abs register-btn">REGISTER NOW</div>
  </div>

  <div class="abs divider"></div>
  <h3 class="abs more-title" style="font-weight:400">More Information about 15-Hour CE package:</h3>
  <ul class="abs bullets more-list">
    <li>Course Format - immediately downloadable PDF file</li>
    <li>Quiz (Open book) - 70% passing rate required. Take as many times as needed. Average of 15 questions.</li>
    <li>Reporting - Completed CE hours are directly submitted to the IRS within 24 hours.</li>
    <li class="two">Certificate - As soon as CE hours are successfully completed, a certificate will be emailed to you. Per IRS standards, the certificate will be available for you to download for 4 years.</li>
  </ul>

  <aside class="abs req-box">
    <p class="req-intro">This package meets the following IRS requirements for registered tax-preparer continuing education:</p>
    <p class="req-main">15-hour per year<br>(beginning in calendar year 2013)</p>
    <p class="req-list">2 hours of ethics<br>3 hours of federal tax law updates<br>10 hours of other federal tax law</p>
  </aside>

  <div class="abs promo promo-a">RTRP Test Simulator Package Only $79.90 - Click for details</div>
  <div class="abs promo promo-b">Combo Package Only $99.90 -- Click for details</div>

  <div class="abs col-head col-1"><span class="icon-chip"></span>Testimonials</div>
  <div class="abs vrule" style="left:422px"></div>
  <div class="abs col-head col-2"><span class="icon-chip"></span>Who we are?</div>
  <div class="abs vrule" style="left:778px"></div>
  <div class="abs col-head col-3">Why us?
    <svg class="slider-arrows" width="28" height="14" viewBox="0 0 28 14"><path d="M8 1L2 7l6 6M20 1l6 6-6 6" fill="none" stroke="#999" stroke-width="2"/></svg>
  </div>

  <p class="abs quote"><span class="quote-mark">“</span>Great reading materials! I learned a lot that I did not know previously. I'm so glad I chose your program!!!!! ”</p>
  <p class="abs author">-Dana.WR</p>
  <p class="abs who-text">We are your official source for IRS Registered Tax Preparer CE training. Our prices are reasonable, and our courses will help you better understand taxes in an efficient manner.</p>
  <div class="abs badge" role="img" aria-label="Approved provider badge"></div>
  <p class="abs why-text">Click here to see our approved provider link at IRS website</p>

  <div class="abs info-bar">
    <span>IRS Latest Information Link ( Click button to open IRS document or link)</span>
    <div class="bulletin-btn">RTRP Test Candidate Information Bulletin</div>
  </div>

  <div class="abs ssl-badge" role="img" aria-label="Secure connection badge"></div>
  <div class="abs accreditor"><i></i>APPROVED<br>CONTINUING EDUCATION<br>ACCREDITOR</div>
  <p class="abs partner">LedgrUMs.com</p>
  <ul class="abs footer-nav">
    <li>Home</li><li>Courses</li><li>FAQ</li><li>Testimonials</li><li>Contact</li><li>Sign In</li><li>Register</li>
  </ul>
</main>

<footer class="abs site-footer">
  <p class="abs copyright">Copyright &nbsp;©&nbsp; 2012 &nbsp; www.7782-qx.com &nbsp;&nbsp; All rights reserved.</p>
  <div class="abs social"><i></i><i></i></div>
</footer>

</body>
</html>
```